Wesbite design for Investment Firm

We want a basic (clean) website that follows the form, fonts and colors of our attachments. This is for a financial investment management firm, but we have a boutique (anti-Wall Street) approach. Site should have an Home Page (Logo up top - room for basic copy on bottom, Philosophy Page (room for Quarterly Letter attachment and basic copy, Performance Page (room for Performance Overview and Performance Analysis and basic copy), Team Page, Commentary Page and Contact

Reason: Some designers have asked for an extension. Again, please only use image of Train Station or Train Station Logo in design.

Target Market(s)

Small and mid-size financial advisors from across the country

Industry/Entity Type

Financial

Number of Pages Required

5+ page

Font styles to use
Other font styles liked:
• Palotino Linotype

Colors
3176b5
cfdeed
ffffff

Requirements
Must have
• Please refer to existing site www.qlvor.example. Of note, this is too complex / cluttered. We simply want Blur, Grey and White consistent with attachments. The copy is pretty good, but will be simplified (and no quotes)
Should not have
• No images other than train station logo and / or train station image

```html
<!DOCTYPE html>
<html lang="en">
<head>
<meta charset="utf-8">
<title>Hartwell Investment Company</title>
<link rel="stylesheet" href="https://fonts.googleapis.com/css2?family=EB+Garamond:wght@400;500&family=Lato:wght@400;700;900&display=swap">
<style>
:root{
  --stage:#b3b3b3;
  --navy:#1b1f86;
  --navy-deep:#0e0f6e;
  --panel:#2e2a8c;
  --orange:#f7941d;
  --gold:#a8832a;
  --ink:#444;
  --muted:#666;
  --line:#e3e3e3;
  --accent:#3176b5;
  --footer-link:#c6c8ef;
  --berry:#8c3a4c;
}
*{box-sizing:border-box;margin:0;padding:0}
html,body{width:1200px;height:1200px;overflow:hidden;background:var(--stage)}
body{font-family:"Lato",sans-serif}
.stage{position:absolute;left:0;top:0;width:1500px;height:1500px;transform:scale(.8);transform-origin:0 0}
.site{position:absolute;left:275px;top:0;width:948px;height:1500px;background:#fff;overflow:hidden}
.abs{position:absolute}

/* header */
.header{left:0;top:0;width:948px;height:80px;background:linear-gradient(90deg,#d9dadc,#eef0f1 50%,#d4d6d8);border-top:3px solid var(--navy-deep)}
.brand{left:0;width:948px;top:4px;text-align:center;font-family:"EB Garamond",serif;font-size:26px;color:var(--navy)}
.tagline{left:0;width:948px;top:34px;text-align:center;font-family:"EB Garamond",serif;font-size:11px;color:var(--gold)}
.nav{left:224px;top:55px;display:flex;align-items:center;font-size:11px;color:#555;height:22px}
.nav span{margin-right:24px}
.nav .current{border:2px solid var(--navy);color:var(--navy);padding:2px 8px;margin-right:14px}
.nav .login{border:2px solid var(--orange);color:var(--orange);border-radius:5px;padding:1px 11px;margin-right:3px}
.nav .signup{background:var(--orange);color:#fff;border-radius:5px;padding:3px 11px;margin:0}

/* hero */
.hero{left:0;top:80px;width:948px;height:361px;background:linear-gradient(100deg,#3a3d43 0%,#6d7a6a 25%,#8a9097 45%,#4b4e55 70%,#1f2230 100%)}
.welcome{left:150px;top:92px;font-size:42px;font-weight:900;color:#fff;letter-spacing:.5px}
.hero-copy{left:150px;top:152px;width:250px;font-size:11.5px;line-height:17.5px;color:#f2f2f2}
.join{left:149px;top:223px;width:118px;height:34px;background:var(--orange);border-radius:6px;color:#fff;font-size:11px;font-weight:700;display:flex;align-items:center;justify-content:center}

/* about */
.about-title{left:150px;top:461px;font-size:21px;color:var(--ink)}
.about-rule{left:150px;top:492px;width:90px;height:2px;background:var(--accent)}
.station{left:149px;top:523px;width:325px;height:205px;background:linear-gradient(160deg,#6d6660 0%,#c9ccd0 45%,#eef0f2 60%,#3a3a3a 100%)}
.about-panel{left:194px;top:674px;width:388px;height:227px;background:var(--panel);color:#fff;padding:20px 19px;box-shadow:0 2px 4px rgba(0,0,0,.25)}
.about-panel h2{font-size:13px;font-weight:700;margin-bottom:15px}
.about-panel p{font-size:9.8px;line-height:17.6px;margin-bottom:17px}

/* side cards */
.card{left:611px;width:159px;border:2px solid var(--line);border-radius:5px;background:#fff;box-shadow:0 1px 3px rgba(0,0,0,.08)}
.card-letter{top:522px;height:291px}
.card-news{top:841px;height:239px}
.card-label{position:absolute;left:9px;top:8px;font-size:9px;font-weight:700;color:var(--navy-deep)}
.letter-cover{position:absolute;left:9px;top:26px;width:140px;height:181px;border:1px solid #555;background:linear-gradient(180deg,#eeeeee 0%,#fafafa 35%,#fff 100%)}
.btn{position:absolute;left:12px;width:136px;height:24px;border-radius:5px;color:#fff;font-size:9.5px;font-weight:700;display:flex;align-items:center;justify-content:center}
.btn-navy{background:var(--navy-deep)}
.btn-orange{background:var(--orange)}
.news-title{position:absolute;left:9px;top:22px;font-size:12px;line-height:12px;color:var(--orange)}
.news-date{position:absolute;left:11px;top:53px;font-size:7px;font-weight:700;color:var(--navy-deep)}
.news-body{position:absolute;left:9px;top:70px;width:135px;font-size:8.5px;line-height:17.6px;color:#444}

/* footer */
.footer{left:0;top:1146px;width:948px;height:354px;background:linear-gradient(180deg,#1a1a92 0%,#15158a 55%,#1f2a96 100%)}
.foot-h{font-size:11px;font-weight:700;color:#fff}
.foot-list{list-style:none;font-size:9px;line-height:17.6px;color:var(--footer-link);margin-top:6px}
.foot-list .hot{color:var(--orange)}
.foot-list .hot-u{color:var(--orange);text-decoration:underline}
.map{left:474px;top:45px;width:138px;height:154px;border-radius:5px;background:linear-gradient(135deg,#c9d4de,#b4c3d1)}
.contact{left:480px;top:207px;font-size:9px;line-height:13px;color:#fff}
.contact-row{display:flex;gap:5px;align-items:flex-start;margin-bottom:4px}
.field{left:631px;width:143px;border-bottom:1px solid #6a6cc0;font-size:9px;color:var(--footer-link);padding-bottom:4px}
.subscribe{left:632px;top:166px;width:72px;height:20px;border-radius:5px;background:var(--berry);color:#fff;font-size:9px;font-weight:700;display:flex;align-items:center;justify-content:center}
.legal{left:0;width:948px;text-align:center;font-size:9px;color:#fff}
</style>
</head>
<body>
<div class="stage">
  <div class="site">
    <header class="header abs">
      <div class="brand abs">Hartwell Investment Company</div>
      <div class="tagline abs">Separately Managed Accounts</div>
      <nav class="nav abs">
        <span class="current">Home</span>
        <span>Philosophy</span>
        <span>Performance</span>
        <span>Team</span>
        <span>Letters</span>
        <span style="margin-right:10px">Commentary</span>
        <span class="login">Login</span>
        <span class="signup">Signup</span>
      </nav>
    </header>

    <section class="hero abs" role="img" aria-label="Photo of two advisers meeting at an outdoor table with a laptop showing charts">
      <div class="welcome abs">WELCOME</div>
      <p class="hero-copy abs">The high expectations of our original investors is a key contributor to our value driven investment philosophy.</p>
      <div class="join abs">JOIN US</div>
    </section>

    <h1 class="about-title abs" style="font-weight:400">About Us</h1>
    <div class="about-rule abs"></div>
    <div class="station abs" role="img" aria-label="Photo of the historic wooden train station"></div>
    <article class="about-panel abs">
      <h2>Hartwell Investment Company</h2>
      <p>We founded Hartwell Investment Company in 1999, initially managing wealth from our family and friends in the town of Hartwell. The high expectations of our original investors is a key contributor to our value driven investment philosophy.</p>
      <p>Based in Fairview, TX, we manage assets for both individuals and institutions. Our investment methodology stresses absolute returns vs. relative performance, blending a combination of fundamental analysis, discipline and patience with the goal of preserving and compounding capital.</p>
    </article>

    <aside class="card card-letter abs">
      <div class="card-label">Investment Adviser's Letter</div>
      <div class="letter-cover" role="img" aria-label="Cover page of the quarterly investment adviser's letter with a station sketch"></div>
      <div class="btn btn-navy" style="top:219px">Read</div>
      <div class="btn btn-orange" style="top:251px">Download PDF</div>
    </aside>

    <aside class="card card-news abs">
      <div class="card-label">Latest Commentary</div>
      <div class="news-title">Core Equity Portfolio<br>Q2 2017</div>
      <div class="news-date">AUGUST 10, 2017</div>
      <p class="news-body">Based on our estimate of fair value relative to the company's current stock price, we determine each company's current margin of safety in the Core Equity...</p>
      <div class="btn btn-orange" style="top:191px">Read More</div>
    </aside>

    <footer class="footer abs">
      <div class="abs" style="left:184px;top:23px">
        <div class="foot-h">Site Map</div>
        <ul class="foot-list">
          <li>Home</li><li>Philosophy</li><li>Performance</li><li>Team</li><li>Letters</li><li>Commentary</li>
          <li class="hot">Login</li><li class="hot">Signup</li>
        </ul>
      </div>
      <div class="abs" style="left:302px;top:23px">
        <div class="foot-h">Quick Links</div>
        <ul class="foot-list">
          <li class="hot-u">Performance Overview</li><li>Performance Analysis</li><li>Verification Statement</li><li>Hartwell ADV Part 2</li>
        </ul>
      </div>
      <div class="foot-h abs" style="left:474px;top:23px">Contact Us</div>
      <div class="map abs" role="img" aria-label="Street map showing the office location"></div>
      <div class="contact abs">
        <div class="contact-row">
          <svg width="9" height="13" viewBox="0 0 9 13"><path d="M4.5 0A4.5 4.5 0 0 0 0 4.5C0 8 4.5 13 4.5 13S9 8 9 4.5A4.5 4.5 0 0 0 4.5 0Zm0 6.3a1.8 1.8 0 1 1 0-3.6 1.8 1.8 0 0 1 0 3.6Z" fill="#5cb85c"/></svg>
          <div>1200 Maple Crest Avenue,<br>Suite 410<br>Fairview, TX 75000</div>
        </div>
        <div class="contact-row" style="margin-left:-4px">
          <svg width="11" height="11" viewBox="0 0 24 24"><path d="M6.6 10.8a15 15 0 0 0 6.6 6.6l2.2-2.2c.3-.3.7-.4 1-.2 1.1.4 2.3.6 3.6.6.6 0 1 .4 1 1V20c0 .6-.4 1-1 1A17 17 0 0 1 3 4c0-.6.4-1 1-1h3.5c.6 0 1 .4 1 1 0 1.3.2 2.5.6 3.6.1.3 0 .7-.2 1Z" fill="#5cb85c"/></svg>
          <div>555.014.7250</div>
        </div>
        <div class="contact-row" style="margin-left:-4px">
          <svg width="11" height="9" viewBox="0 0 11 9"><rect width="11" height="9" rx="1" fill="#5cb85c"/><path d="M0.5 1 5.5 5 10.5 1" stroke="#1a1a92" fill="none"/></svg>
          <div>info@qlvor.example</div>
        </div>
      </div>
      <div class="foot-h abs" style="left:631px;top:23px">Subscribe to our Newsletter</div>
      <div class="field abs" style="top:43px">your name</div>
      <div class="field abs" style="top:71px">your email</div>
      <div class="field abs" style="top:131px">your message</div>
      <div class="subscribe abs">Subscribe</div>
      <div class="legal abs" style="top:310px"><span style="margin-right:12px">Terms &amp; Condition</span>Privacy</div>
      <div class="legal abs" style="top:334px">qlvor.example 2017. All rights reserved.</div>
    </footer>
  </div>
</div>
</body>
</html>
```